Vorelan.com Personal Trainer/Fitness Website

I want a website to market my personal training/Outdoor Bootcamp Class services, as well as to ditribute nutrivex. I need a logo as well I included an address for the Harbor Gales 1975 logo. I'd like Vorelan in place of Harbor Gales, and in Black and white, just different enough so I can't get sued by the PBL.
https://www.pictofind.example/imgres?imgurl=http%3A%2F%2Fwww.darnell-quibury.example%2Fwp-content%2Fuploads%2F2014%2F01%2Fgales_logo4.jpg&imgrefurl=http%3A%2F%2Fwww.darnell-quibury.example%2Fpbl-logo-redesigns-harbor-gales%2F&docid=_qkwzR7TBAgXpL&tbnid=m4tpU8KdOXjnRP%3A&w=600&h=450&client=ms-android-carrier&bih=512&biw=360&ved=0ahUKEwiRtpgyp9HMAhUTwGMKHRPMBWMQMwg6KBQwFA&iact=mrc&uact=8.
It should be about 5 pages 1. home 2. about 3. Services 4. Blog/Videos and programs 5. Contact.
http://www.dorvinfitness.example.uk/ is a website I like the style of.

Target Market(s)

Seattle area

Industry/Entity Type

Fitness

Coding

Coded - Design and coding required

Number of Pages Required

4 page

Font styles to use
Serif
Sans Serif

Requirements
Must have
• A minimal look
Nice to have
• A logo similar to the 1975 Harbor Galewinds Logo, with a Small Milo Brandt ripping his shirt open(with a picture of the logo on his shirt, picture within picture) to turn into Ironjaw in the center. Skyline is black, Background and small figure white(with black logo on shirt)

```html
<!DOCTYPE html>
<html lang="en">
<head>
<meta charset="utf-8">
<title>Vorelan – Fitness &amp; Trainings</title>
<link href="https://fonts.googleapis.com/css2?family=Exo+2:wght@600;700&family=Lato:wght@400;700&family=Montserrat:wght@600;700&display=swap" rel="stylesheet">
<style>
:root{
  --black:#000;
  --ink:#111;
  --dark:#1b1b1b;
  --panel:#2b2b2b;
  --mid:#3c3c3c;
  --grey:#5b5b5b;
  --light:#d8d8d8;
  --white:#fff;
  --text:#333;
  --green:#a9d18e;
}
*{margin:0;padding:0;box-sizing:border-box}
html,body{width:1200px;height:3285px;overflow:hidden}
body{position:relative;background:var(--white);font-family:"Lato",Arial,sans-serif;color:var(--text)}
.abs{position:absolute}
.head-font{font-family:"Exo 2","Arial Black",sans-serif;font-weight:700;letter-spacing:1px}
.btn{position:absolute;display:flex;align-items:center;justify-content:center;font-family:"Montserrat",Arial,sans-serif;font-weight:700;font-size:16px;color:var(--white);background:var(--ink);letter-spacing:.5px}
.btn.grey{background:var(--mid)}
.center{text-align:center}

/* header */
.site-header{top:0;left:0;width:1200px;height:136px;background:var(--white)}
.brand{left:78px;top:86px;display:flex;align-items:center;gap:10px;font-family:"Exo 2",sans-serif;font-weight:700;font-size:30px;letter-spacing:1px;color:var(--ink)}
.brand-dot{width:16px;height:16px;border-radius:50%;background:var(--ink)}
.member-btn{left:904px;top:22px;width:215px;height:44px;border-radius:4px;font-size:15px}
.phone{left:754px;top:84px;display:flex;align-items:center;gap:10px;font-family:"Montserrat",sans-serif;font-weight:700;font-size:19px;color:var(--ink)}
.phone-ico{width:32px;height:32px;border-radius:50%;background:#bbb;display:flex;align-items:center;justify-content:center}
.social{width:34px;height:34px;border-radius:50%}

/* nav */
.main-nav{top:136px;left:0;width:1200px;height:46px;background:var(--black)}
.nav-item{position:absolute;top:0;height:46px;display:flex;align-items:center;justify-content:center;font-family:"Montserrat",sans-serif;font-weight:600;font-size:15px;color:var(--white);border-right:1px solid #555}
.nav-item.active{background:#444}

/* hero */
.hero{top:182px;left:0;width:1200px;height:611px;background:linear-gradient(110deg,#3e3e3e 0%,#6e6e6e 40%,#8a8a8a 60%,#4d4d4d 100%)}
.hero-line1{left:83px;top:282px;font-size:38px;color:var(--white)}
.hero-line2{left:83px;top:334px;font-size:46px;color:var(--white);letter-spacing:2px}
.hero-btn{left:88px;top:425px;width:192px;height:45px;border-radius:3px}
.dot{top:522px;width:14px;height:14px;border-radius:50%;background:#aaa}
.dot.on{background:var(--white)}

/* promo */
.promo{top:793px;left:0;width:1200px;height:177px;background:linear-gradient(90deg,#262626,#1d1d1d 50%,#262626)}
.promo-title{font-family:"Montserrat",sans-serif;font-weight:600;font-size:24px;color:var(--white)}
.promo-btn{height:42px;border-radius:3px;background:#3a3a3a}
.offer{left:410px;top:-13px;width:381px;height:190px;background:#3a3a3a;border:1px solid #555}
.offer-tab{left:80px;top:140px;width:221px;height:50px;background:var(--dark);display:flex;align-items:center;justify-content:center;font-family:"Montserrat",sans-serif;font-weight:700;font-size:22px;color:var(--white)}

/* services */
.services{top:970px;left:0;width:1200px;height:524px;background:linear-gradient(180deg,#5a5a5a,#4a4a4a)}
.section-title{font-size:32px;color:var(--white);width:1200px;text-align:center}
.service-icon{width:118px;height:118px;border-radius:50%;background:var(--black);border:4px solid var(--white);display:flex;align-items:center;justify-content:center}
.service-name{width:300px;text-align:center;font-family:"Montserrat",sans-serif;font-weight:600;font-size:19px;color:var(--white)}
.service-desc{width:300px;text-align:center;font-size:13px;line-height:22px;color:var(--white)}
.plus{width:26px;height:26px;background:var(--white);color:var(--ink);font-weight:700;display:flex;align-items:center;justify-content:center;font-size:20px;line-height:1}

/* welcome */
.welcome{top:1494px;left:0;width:1200px;height:291px;background:var(--white)}
.welcome-title{top:32px;width:1200px;text-align:center;font-size:31px;color:#333}
.welcome-text{left:114px;top:119px;width:974px;text-align:center;font-size:15px;line-height:24px;color:#333}

/* amenities */
.amenities{top:1785px;left:0;width:1200px;height:414px;overflow:hidden}
.amen-left{left:0;top:0;width:520px;height:414px;background:linear-gradient(135deg,#7d9ab8 0%,#8f8b6e 45%,#5e6b4d 100%)}
.amen-right{left:720px;top:0;width:480px;height:414px;background:linear-gradient(135deg,#b8b8b8,#6d6d6d)}

/* feature boxes */
.feature{top:2247px;width:324px;height:177px;background:linear-gradient(135deg,#6b6b6b,#4e4e4e);display:flex;flex-direction:column;align-items:center;justify-content:flex-end;padding-bottom:28px;gap:10px}
.feature-name{font-size:24px;color:var(--white);text-align:center;line-height:28px}

/* events */
.events{top:2488px;left:0;width:1200px;height:289px;background:var(--black)}
.events-photo{left:0;top:0;width:598px;height:289px;background:linear-gradient(135deg,#b9b3ab,#8a8a8a 50%,#5b5b5b)}

/* footer */
.footer{top:2777px;left:0;width:1200px;height:508px;background:linear-gradient(180deg,#1f1f1f,#141414)}
.footer-h{font-family:"Montserrat",sans-serif;font-weight:600;font-size:19px;color:var(--white);display:flex;align-items:center;gap:10px}
.field{background:transparent;border:1px solid #444;color:#ddd;font-size:13px;padding:10px 12px}
.link-list{list-style:none;font-size:14px;color:#ddd}
.link-list li{height:27px}
.link-list li::before{content:"›";margin-right:10px}
.copyright{left:0;top:3247px;width:1200px;height:38px;background:#3c3c3c;color:#ddd;font-size:13px;display:flex;align-items:center;justify-content:center}
</style>
</head>
<body>

<header class="site-header abs">
  <div class="brand abs"><span class="brand-dot"></span>VORELAN</div>
  <div class="btn member-btn">
    <svg width="20" height="20" viewBox="0 0 20 20" style="margin-right:8px"><circle cx="10" cy="6" r="4" fill="#fff"/><path d="M2 19c0-5 4-8 8-8s8 3 8 8z" fill="#fff"/></svg>BECOME A MEMBER
  </div>
  <div class="phone abs">
    <span class="phone-ico"><svg width="16" height="16" viewBox="0 0 16 16"><path d="M3 1l3 3-2 2c1 2 3 4 5 5l2-2 3 3-2 3C7 15 1 9 1 3z" fill="#fff"/></svg></span>
    123-456-7890
  </div>
  <span class="social abs" style="left:946px;top:82px;background:#2a5bab"></span>
  <span class="social abs" style="left:997px;top:82px;background:#2aa6e0"></span>
  <span class="social abs" style="left:1045px;top:82px;background:#c4262b"></span>
  <span class="social abs" style="left:1086px;top:82px;background:#dc4b3b"></span>
</header>

<nav class="main-nav abs">
  <div class="nav-item active" style="left:81px;width:112px;border-left:1px solid #555">HOME</div>
  <div class="nav-item" style="left:193px;width:135px">ABOUT</div>
  <div class="nav-item" style="left:328px;width:176px">SERVICES</div>
  <div class="nav-item" style="left:504px;width:131px">BLOG</div>
  <div class="nav-item" style="left:635px;width:142px">VIDEOS</div>
  <div class="nav-item" style="left:777px;width:198px">PROGRAMS</div>
  <div class="nav-item" style="left:975px;width:146px">CONTACT</div>
</nav>

<section class="hero abs" role="img" aria-label="Trainer coaching an athlete doing kettlebell push-ups in a gym">
  <div class="hero-line1 abs head-font">STRENGTH AT WORK</div>
  <div class="hero-line2 abs head-font">FITNESS &amp; TRAININGS</div>
  <div class="btn hero-btn">GET STARTED</div>
  <span class="dot on abs" style="left:558px"></span>
  <span class="dot abs" style="left:591px"></span>
  <span class="dot abs" style="left:624px"></span>
</section>

<section class="promo abs">
  <div class="promo-title abs center" style="left:41px;top:32px;width:400px">Get Access To All Facilites</div>
  <div class="btn promo-btn" style="left:136px;top:89px;width:214px">SUBSCRIBE NOW</div>
  <div class="offer abs">
    <div class="promo-title abs center" style="left:0;top:20px;width:381px;font-size:28px">Signup For 6 Month</div>
    <div class="abs center" style="left:0;top:64px;width:381px;font-family:Montserrat,sans-serif;font-weight:700;font-size:33px;color:var(--green)">Get 30% off</div>
    <div class="offer-tab abs">SIGN UP!</div>
  </div>
  <div class="promo-title abs center" style="left:763px;top:32px;width:400px">Offer Free Consultation</div>
  <div class="btn promo-btn" style="left:839px;top:89px;width:245px">GET CONSULTATION</div>
</section>

<section class="services abs">
  <div class="section-title abs head-font" style="top:60px">OUR SERVICES</div>
  <div class="abs" style="left:423px;top:117px;width:354px;height:2px;background:#bbb"></div>
  <p class="abs center" style="left:219px;top:150px;width:762px;font-size:14px;line-height:24px;color:#fff">Our coaches build every plan around your goals, your pace and your schedule. Train one to one, join a group outdoors or follow a program online with steady support.</p>

  <div class="service-icon abs" style="left:127px;top:211px"><svg width="60" height="60" viewBox="0 0 60 60"><circle cx="22" cy="14" r="7" fill="#fff"/><rect x="12" y="24" width="20" height="14" fill="#fff"/><rect x="6" y="40" width="48" height="5" fill="#fff"/><rect x="38" y="28" width="4" height="12" fill="#fff"/></svg></div>
  <div class="service-name abs" style="left:36px;top:352px">Personal Training</div>
  <div class="service-desc abs" style="left:36px;top:380px">One to one coaching sessions,<br>tailored to your body and aims</div>
  <div class="plus abs" style="left:173px;top:462px">+</div>

  <div class="service-icon abs" style="left:407px;top:211px"><svg width="64" height="60" viewBox="0 0 64 60"><g fill="#fff"><circle cx="14" cy="12" r="6"/><circle cx="32" cy="12" r="6"/><circle cx="50" cy="12" r="6"/><rect x="9" y="20" width="10" height="18"/><rect x="27" y="20" width="10" height="18"/><rect x="45" y="20" width="10" height="18"/><rect x="9" y="38" width="4" height="16"/><rect x="15" y="38" width="4" height="16"/><rect x="27" y="38" width="4" height="16"/><rect x="33" y="38" width="4" height="16"/><rect x="45" y="38" width="4" height="16"/><rect x="51" y="38" width="4" height="16"/></g></svg></div>
  <div class="service-name abs" style="left:316px;top:352px">Outdoor Bootcamp Classes</div>
  <div class="service-desc abs" style="left:316px;top:380px">High energy group workouts,<br>held outside in every season</div>
  <div class="plus abs" style="left:453px;top:462px">+</div>

  <div class="service-icon abs" style="left:697px;top:211px"><svg width="60" height="60" viewBox="0 0 60 60"><g fill="#fff"><circle cx="36" cy="10" r="6"/><path d="M20 20l16-2 6 12 10 2-1 4-13-3-5-7-4 10 8 8-3 12-4-1 2-9-9-7-6 8-10-2 2-4 6 1z"/></g></svg></div>
  <div class="service-name abs" style="left:606px;top:352px">Outdoor Group Training</div>
  <div class="service-desc abs" style="left:606px;top:380px">Small team sessions in parks,<br>built on pace and teamwork</div>
  <div class="plus abs" style="left:743px;top:462px">+</div>

  <div class="service-icon abs" style="left:955px;top:211px"><svg width="60" height="60" viewBox="0 0 60 60"><g fill="#fff"><rect x="6" y="8" width="48" height="34" rx="2"/><rect x="24" y="44" width="12" height="6"/><rect x="16" y="50" width="28" height="4"/></g><circle cx="24" cy="22" r="5" fill="#000"/><rect x="17" y="29" width="14" height="10" fill="#000"/><rect x="36" y="18" width="12" height="3" fill="#000"/><rect x="36" y="25" width="12" height="3" fill="#000"/></svg></div>
  <div class="service-name abs" style="left:864px;top:352px">Online Coaching</div>
  <div class="service-desc abs" style="left:864px;top:380px">Remote plans and check ins,<br>guided from wherever you are</div>
  <div class="plus abs" style="left:1001px;top:462px">+</div>
</section>

<section class="welcome abs">
  <div class="welcome-title abs head-font">WELCOME TO VORELAN</div>
  <div class="abs" style="left:170px;top:86px;width:860px;height:1px;background:#ccc"></div>
  <div class="abs" style="left:558px;top:85px;width:77px;height:3px;background:#222"></div>
  <p class="welcome-text abs">Vorelan is a Seattle based training team that helps busy people get stronger, fitter and more confident. We mix personal coaching, outdoor bootcamp classes and practical nutrition advice into simple plans you can keep. Every member gets a clear starting point, honest feedback and a coach who checks in often, so progress stays steady and training stays fun all year long.</p>
  <div class="btn" style="left:547px;top:214px;width:106px;height:24px;font-size:11px;border-radius:2px">READ MORE</div>
</section>

<section class="amenities abs">
  <div class="amen-left abs" role="img" aria-label="Outdoor bootcamp group doing push-ups on mats in a park"></div>
  <div class="amen-right abs" role="img" aria-label="Gym floor with rows of treadmills and cardio machines"></div>
  <svg class="abs" style="left:0;top:0" width="1200" height="414" viewBox="0 0 1200 414">
    <polygon points="438,0 832,0 756,414 366,414" fill="#0d0d0d"/>
    <circle cx="208" cy="206" r="48" fill="rgba(0,0,0,.2)" stroke="#fff" stroke-width="4"/>
    <polygon points="194,182 194,230 232,206" fill="#fff"/>
  </svg>
  <div class="abs center head-font" style="left:418px;top:62px;width:400px;font-size:30px;color:#fff">STATE OF THE ART</div>
  <div class="abs center head-font" style="left:418px;top:106px;width:400px;font-size:42px;color:#fff">AMENITIES</div>
  <p class="abs center" style="left:418px;top:186px;width:400px;font-family:Montserrat,sans-serif;font-size:17px;line-height:29px;color:#fff">FEATURING THE BEST<br>EQUIPMENT, LOCKER ROOMS,<br>SMOOTHIE BAR &amp; MORE.</p>
  <div class="btn grey" style="left:488px;top:306px;width:160px;height:46px;border-radius:3px">LEARN MORE</div>
</section>

<div class="feature abs" style="left:81px" role="img" aria-label="Coach meeting a client for a consultation">
  <svg width="70" height="44" viewBox="0 0 70 44"><g fill="#fff"><circle cx="16" cy="8" r="6"/><circle cx="54" cy="8" r="6"/><rect x="10" y="16" width="12" height="14"/><rect x="48" y="16" width="12" height="14"/><rect x="20" y="24" width="30" height="4"/><rect x="33" y="28" width="4" height="14"/></g></svg>
  <div class="feature-name head-font">Free Consultation</div>
</div>
<div class="feature abs" style="left:438px" role="img" aria-label="Woman holding an apple">
  <svg width="44" height="46" viewBox="0 0 44 46"><path d="M22 12c-6-4-18-3-18 12 0 12 9 22 18 20 9 2 18-8 18-20 0-15-12-16-18-12z" fill="#fff"/><rect x="21" y="2" width="3" height="10" fill="#fff"/></svg>
  <div class="feature-name head-font">Nutrition Guidance</div>
</div>
<div class="feature abs" style="left:795px" role="img" aria-label="Personal trainer guiding a client on a machine">
  <svg width="60" height="40" viewBox="0 0 60 40"><g fill="#fff"><circle cx="18" cy="8" r="6"/><rect x="12" y="16" width="12" height="14"/><rect x="28" y="20" width="24" height="4"/><rect x="48" y="10" width="4" height="28"/><rect x="8" y="34" width="46" height="4"/></g></svg>
  <div class="feature-name head-font">Get A<br>Personal Trainer</div>
</div>

<section class="events abs">
  <div class="events-photo abs" role="img" aria-label="Group of people stretching together at an outdoor fitness event"></div>
  <div class="abs head-font" style="left:637px;top:40px;font-size:28px;line-height:44px;color:#fff">We Organize &amp; Participate<br>In Group Events</div>
  <p class="abs" style="left:637px;top:142px;width:500px;font-size:13px;line-height:24px;color:#ddd">Join our runs, park challenges and charity workouts held across the city. Bring a friend, meet the team and train together with real community energy.</p>
  <div class="btn grey" style="left:639px;top:204px;width:143px;height:46px;border-radius:2px;font-size:15px">LEARN MORE</div>
</section>

<footer class="footer abs">
  <div class="abs" style="left:81px;top:55px;width:721px;height:65px;border:1px solid #444"></div>
  <div class="footer-h abs" style="left:98px;top:74px;font-weight:400;font-family:Lato,sans-serif;font-size:18px">
    <svg width="24" height="24" viewBox="0 0 24 24"><circle cx="12" cy="12" r="11" fill="#555"/><rect x="6" y="8" width="12" height="9" fill="#ddd"/><path d="M6 8l6 5 6-5" fill="none" stroke="#555" stroke-width="1.5"/></svg>Newsletter Signup
  </div>
  <div class="abs" style="left:307px;top:70px;width:383px;height:36px;background:#fff;font-size:12px;color:#333;padding:10px">Enter your email here</div>
  <div class="abs" style="left:690px;top:70px;width:100px;height:36px;background:#000;color:#fff;font-size:13px;display:flex;align-items:center;justify-content:center">SUBSCRIBE</div>
  <div class="abs" style="left:843px;top:74px;font-family:Montserrat,sans-serif;font-weight:600;font-size:17px;color:#fff">Follow Us</div>
  <span class="social abs" style="left:947px;top:68px;border:2px solid #aaa"></span>
  <span class="social abs" style="left:986px;top:68px;border:2px solid #aaa"></span>
  <span class="social abs" style="left:1028px;top:68px;border:2px solid #aaa"></span>
  <span class="social abs" style="left:1074px;top:68px;border:2px solid #aaa"></span>

  <div class="footer-h abs head-font" style="left:81px;top:162px;font-size:24px;font-family:'Exo 2',sans-serif;font-weight:700">
    <svg width="24" height="24" viewBox="0 0 24 24"><circle cx="12" cy="12" r="10" fill="none" stroke="#fff" stroke-width="2"/><text x="12" y="17" text-anchor="middle" font-size="13" fill="#fff" font-family="Arial, sans-serif" font-weight="700">?</text></svg>QUICK INQUIRY
  </div>
  <div class="field abs" style="left:81px;top:234px;width:226px;height:38px">Name</div>
  <div class="field abs" style="left:81px;top:291px;width:226px;height:38px">Email Address</div>
  <div class="field abs" style="left:81px;top:348px;width:226px;height:38px">Phone Number</div>
  <div class="field abs" style="left:324px;top:234px;width:230px;height:95px">Message</div>
  <div class="abs" style="left:324px;top:348px;width:230px;height:38px;background:#444;color:#fff;font-family:Montserrat,sans-serif;font-weight:600;font-size:14px;display:flex;align-items:center;justify-content:center">SUBMIT</div>

  <div class="abs" style="left:602px;top:160px;width:1px;height:270px;background:#333"></div>
  <div class="abs" style="left:832px;top:160px;width:1px;height:270px;background:#333"></div>

  <div class="footer-h abs" style="left:628px;top:170px;font-size:18px">
    <svg width="18" height="22" viewBox="0 0 18 22"><rect x="1" y="3" width="16" height="18" fill="none" stroke="#fff" stroke-width="2"/><rect x="5" y="0" width="8" height="5" fill="#fff"/></svg>Quick Links
  </div>
  <ul class="link-list abs" style="left:628px;top:222px">
    <li>Home</li><li>About</li><li>Services</li><li>Blog</li><li>Videos</li><li>Programs</li><li>Contact</li>
  </ul>

  <div class="footer-h abs" style="left:872px;top:170px;font-size:18px">
    <svg width="22" height="18" viewBox="0 0 22 18"><rect x="1" y="1" width="20" height="16" fill="none" stroke="#fff" stroke-width="2"/><circle cx="8" cy="8" r="3" fill="#fff"/><rect x="13" y="6" width="5" height="2" fill="#fff"/><rect x="13" y="10" width="5" height="2" fill="#fff"/></svg>Contact Information
  </div>
  <svg class="abs" style="left:872px;top:224px" width="14" height="20" viewBox="0 0 14 20"><path d="M7 0a7 7 0 0 1 7 7c0 5-7 13-7 13S0 12 0 7a7 7 0 0 1 7-7z" fill="#bbb"/><circle cx="7" cy="7" r="2.5" fill="#1b1b1b"/></svg>
  <div class="abs" style="left:896px;top:222px;width:230px;font-size:13px;line-height:22px;color:#ccc">VORELAN<br>Seattle area training studio,<br>open daily for members</div>
  <div class="abs" style="left:872px;top:296px;width:250px;height:1px;background:#333"></div>
  <svg class="abs" style="left:872px;top:309px" width="14" height="14" viewBox="0 0 16 16"><path d="M3 1l3 3-2 2c1 2 3 4 5 5l2-2 3 3-2 3C7 15 1 9 1 3z" fill="#bbb"/></svg>
  <div class="abs" style="left:898px;top:307px;font-size:14px;color:#ddd">123-456-7890</div>
  <div class="abs" style="left:872px;top:340px;width:250px;height:1px;background:#333"></div>
  <svg class="abs" style="left:872px;top:360px" width="16" height="12" viewBox="0 0 16 12"><rect x="1" y="1" width="14" height="10" fill="none" stroke="#bbb" stroke-width="1.5"/><path d="M1 1l7 6 7-6" fill="none" stroke="#bbb" stroke-width="1.5"/></svg>
  <div class="abs" style="left:898px;top:357px;font-size:13px;color:#ddd">info@vorelan.com</div>

  <div class="abs" style="left:0;top:458px;width:1200px;height:3px;background:#555"></div>
  <svg class="abs" style="left:580px;top:441px" width="40" height="20" viewBox="0 0 40 20"><path d="M0 20 Q20 -6 40 20z" fill="#555"/><path d="M14 14l6-6 6 6" fill="none" stroke="#ddd" stroke-width="2"/></svg>
</footer>
<div class="copyright abs">COPYRIGHT 2016 VORELAN | ALL RIGHT RESERVED.</div>

</body>
</html>
```